Pyschiatry Experts need Marketing Campaign

Ad(s) developed for print advertising sharing our purpose and services, highlighting our medical care providers. Must be welcoming and inviting while displaying a high level of professionalism expected from a physician's office.

Target Market(s)

Local community

Industry/Entity Type

Psychiatry (Healthcare)

Requirements
Must have
• Staff pictures, 'Medication Management Experts', 'Prompt Appointments', 'ADD/ADHD, Bipolar Disorder, Depression, Anxiety, Schizophrenia, Grief Reaction and others' 'Virtual and In-Person Visits'
Nice to have
• Address: 412 E Marlowe Coeur d'Alene Phone (208)555-7193 website: BrightLoftCare.com Hours: Mon - Thur 7am - 6pm

```html
<!DOCTYPE html>
<html lang="en">
<head>
<meta charset="utf-8">
<title>Brightloft Care – Medication Management Experts</title>
<link href="https://fonts.googleapis.com/css2?family=Tinos:wght@700&family=Roboto+Condensed:wght@500;700&family=Montserrat:wght@500;600&display=swap" rel="stylesheet">
<style>
:root{
  --backdrop:#032a22;
  --forest:#0b3428;
  --teal:#128f7c;
  --teal-deep:#0d7a68;
  --aqua:#1cb89c;
  --lime:#a9e04c;
  --lime-soft:#c4ec6e;
  --ink:#10302a;
  --white:#ffffff;
}
*{box-sizing:border-box;margin:0;padding:0}
html,body{width:1200px;height:1200px;overflow:hidden}
body{background:var(--backdrop);position:relative;font-family:"Roboto Condensed",sans-serif}

.flyer{
  position:absolute;left:247px;top:143px;width:706px;height:914px;overflow:hidden;
  box-shadow:0 10px 40px rgba(0,0,0,.45);
}
.flyer-scene{
  position:absolute;inset:0;
  background:linear-gradient(180deg,#cfe0f2 0%,#e6edf3 28%,#f6f0e2 52%,#f3e8cf 62%,#8b8a78 74%,#2f3a2e 84%,#0e1512 100%);
}
.flyer-scene::after{
  content:"";position:absolute;left:330px;top:600px;width:200px;height:230px;
  background:radial-gradient(ellipse at 50% 30%,rgba(255,240,210,.55),rgba(255,240,210,0) 70%);
}

.headline{
  position:absolute;left:50px;top:34px;
  font-family:"Tinos",serif;font-weight:700;font-size:51px;line-height:50px;color:var(--ink);
}
.services{
  position:absolute;left:48px;top:202px;
  font-family:"Roboto Condensed",sans-serif;font-weight:500;font-size:19.5px;line-height:25px;color:var(--teal-deep);
}

.brand{position:absolute;left:400px;top:36px;width:272px;text-align:center}
.brand-mark{width:66px;height:66px;border-radius:50%;background:var(--aqua);margin:0 auto 10px}
.brand-name{
  font-family:"Tinos",serif;font-weight:700;font-size:30px;line-height:32px;letter-spacing:1px;color:var(--aqua);
}

.providers-label{
  position:absolute;left:48px;top:269px;width:290px;height:34px;background:var(--forest);
  font-family:"Tinos",serif;font-weight:700;font-size:14px;letter-spacing:.3px;color:var(--lime);
  display:flex;align-items:center;justify-content:center;
}
.provider{position:absolute;width:141px;height:211px}
.provider-photo{height:170px;background:radial-gradient(ellipse at 50% 45%,#8d989c 0%,#4b5558 55%,#2a3133 100%)}
.provider-caption{
  height:41px;background:var(--teal);color:var(--white);text-align:center;padding-top:4px;
}
.provider-name{font-family:"Tinos",serif;font-weight:700;font-size:17px;line-height:19px;color:#f4f8ee}
.provider-cred{font-family:"Montserrat",sans-serif;font-weight:500;font-size:9.5px;line-height:13px}

.expert-frame{
  position:absolute;left:405px;top:211px;width:262px;height:300px;
  border:4px solid var(--lime);border-bottom:none;border-radius:26px 26px 0 0;
}
.expert-title{
  position:absolute;left:410px;top:240px;width:262px;text-align:center;font-family:"Tinos",serif;font-weight:700;
}
.expert-title .small{display:block;font-size:24.5px;line-height:25px;color:var(--teal-deep);letter-spacing:.5px}
.expert-title .big{display:block;font-size:41px;line-height:42px;color:var(--ink)}

.conditions{
  position:absolute;left:404px;top:354px;width:263px;height:416px;background:var(--teal);
  border-radius:24px;list-style:none;
}
.condition{
  position:absolute;left:0;width:100%;transform:translateY(-50%);
  display:flex;align-items:center;
  font-weight:700;font-size:27px;line-height:27px;color:var(--white);text-transform:uppercase;
}
.condition svg{position:absolute;left:27px;width:27px;height:27px}
.condition.two-line svg{top:0}
.condition span{margin-left:67px}
.rule{position:absolute;left:22px;width:215px;height:2px;background:rgba(196,236,110,.45)}

.perks{position:absolute;left:48px;top:765px;display:flex;font-weight:500;font-size:21px;line-height:23px;color:var(--white);text-transform:uppercase}
.perk em{font-style:normal;color:var(--lime)}
.perk + .perk{border-left:1.5px solid rgba(255,255,255,.5);margin-left:12px;padding-left:14px}

.contact{position:absolute;left:48px;font-family:"Montserrat",sans-serif;font-weight:500;font-size:17px;color:var(--white);display:flex;align-items:center}
.contact svg{width:22px;height:22px;margin-right:10px}
.contact.phone{top:826px}
.contact.address{top:856px}

.hours-pill{
  position:absolute;left:450px;top:796px;width:160px;height:21px;border-radius:11px;background:var(--lime);
  font-family:"Montserrat",sans-serif;font-weight:600;font-size:11.5px;letter-spacing:1.6px;color:var(--forest);
  display:flex;align-items:center;justify-content:center;
}
.hours{position:absolute;left:404px;top:821px;width:252px;text-align:center;font-family:"Montserrat",sans-serif;font-weight:600;font-size:19px;color:var(--white)}
.website{
  position:absolute;left:399px;top:851px;width:260px;height:28px;
  border-top:1.5px solid rgba(255,255,255,.35);border-bottom:1.5px solid rgba(255,255,255,.35);
  font-family:"Montserrat",sans-serif;font-weight:600;font-size:15px;letter-spacing:2.6px;color:var(--aqua);
  display:flex;align-items:center;justify-content:center;
}
</style>
</head>
<body>
<main class="flyer">
  <div class="flyer-scene" role="img" aria-label="Misty mountain landscape at sunrise with a person meditating on a cliff edge"></div>

  <h1 class="headline">Helping Bodies<br>Helping Minds<br>Helping You</h1>
  <p class="services">Mental Health &amp; Psychiatry Services<br>Migraine &amp; Neurospasticity Intervention</p>

  <div class="brand">
    <div class="brand-mark"></div>
    <div class="brand-name">BRIGHTLOFT<br>CARE</div>
  </div>

  <div class="providers-label">OUR MENTAL HEALTH PROVIDERS</div>

  <figure class="provider" style="left:48px;top:314px">
    <div class="provider-photo" role="img" aria-label="Portrait photo of Evan Harlow"></div>
    <figcaption class="provider-caption"><div class="provider-name">Evan Harlow</div><div class="provider-cred">PMHNP - BC</div></figcaption>
  </figure>
  <figure class="provider" style="left:197px;top:314px">
    <div class="provider-photo" role="img" aria-label="Portrait photo of Meredith Cole"></div>
    <figcaption class="provider-caption"><div class="provider-name">Meredith Cole</div><div class="provider-cred">PMHNP - BC</div></figcaption>
  </figure>
  <figure class="provider" style="left:48px;top:533px">
    <div class="provider-photo" role="img" aria-label="Portrait photo of Grant Whitaker"></div>
    <figcaption class="provider-caption"><div class="provider-name">Grant Whitaker</div><div class="provider-cred">PMHNP - BC</div></figcaption>
  </figure>
  <figure class="provider" style="left:197px;top:533px">
    <div class="provider-photo" role="img" aria-label="Portrait photo of Lorraine Beckett"></div>
    <figcaption class="provider-caption"><div class="provider-name">Lorraine Beckett</div><div class="provider-cred">PMHNP-BC, DNP</div></figcaption>
  </figure>

  <div class="expert-frame"></div>
  <h2 class="expert-title"><span class="small">MEDICATION</span><span class="small">MANAGEMENT</span><span class="big">EXPERTS</span></h2>

  <ul class="conditions">
    <li class="condition" style="top:45px"><svg viewBox="0 0 28 28"><circle cx="14" cy="14" r="12" fill="none" stroke="#a9e04c" stroke-width="2.4"/><path d="M9 14.5l3.5 3.5 6.5-7" fill="none" stroke="#a9e04c" stroke-width="2.4" stroke-linecap="round" stroke-linejoin="round"/></svg><span>ADD/ADHD</span></li>
    <li class="rule" style="top:67px"></li>
    <li class="condition two-line" style="top:106px"><svg viewBox="0 0 28 28"><circle cx="14" cy="14" r="12" fill="none" stroke="#a9e04c" stroke-width="2.4"/><path d="M9 14.5l3.5 3.5 6.5-7" fill="none" stroke="#a9e04c" stroke-width="2.4" stroke-linecap="round" stroke-linejoin="round"/></svg><span>Bipolar<br>Disorder</span></li>
    <li class="rule" style="top:140px"></li>
    <li class="condition" style="top:166px"><svg viewBox="0 0 28 28"><circle cx="14" cy="14" r="12" fill="none" stroke="#a9e04c" stroke-width="2.4"/><path d="M9 14.5l3.5 3.5 6.5-7" fill="none" stroke="#a9e04c" stroke-width="2.4" stroke-linecap="round" stroke-linejoin="round"/></svg><span>Depression</span></li>
    <li class="rule" style="top:189px"></li>
    <li class="condition" style="top:211px"><svg viewBox="0 0 28 28"><circle cx="14" cy="14" r="12" fill="none" stroke="#a9e04c" stroke-width="2.4"/><path d="M9 14.5l3.5 3.5 6.5-7" fill="none" stroke="#a9e04c" stroke-width="2.4" stroke-linecap="round" stroke-linejoin="round"/></svg><span>Anxiety</span></li>
    <li class="rule" style="top:232px"></li>
    <li class="condition" style="top:255px"><svg viewBox="0 0 28 28"><circle cx="14" cy="14" r="12" fill="none" stroke="#a9e04c" stroke-width="2.4"/><path d="M9 14.5l3.5 3.5 6.5-7" fill="none" stroke="#a9e04c" stroke-width="2.4" stroke-linecap="round" stroke-linejoin="round"/></svg><span>Schizophrenia</span></li>
    <li class="rule" style="top:276px"></li>
    <li class="condition two-line" style="top:314px"><svg viewBox="0 0 28 28"><circle cx="14" cy="14" r="12" fill="none" stroke="#a9e04c" stroke-width="2.4"/><path d="M9 14.5l3.5 3.5 6.5-7" fill="none" stroke="#a9e04c" stroke-width="2.4" stroke-linecap="round" stroke-linejoin="round"/></svg><span>Grief<br>Reaction</span></li>
    <li class="rule" style="top:349px"></li>
    <li class="condition" style="top:376px"><svg viewBox="0 0 28 28"><circle cx="14" cy="14" r="12" fill="none" stroke="#a9e04c" stroke-width="2.4"/><path d="M9 14.5l3.5 3.5 6.5-7" fill="none" stroke="#a9e04c" stroke-width="2.4" stroke-linecap="round" stroke-linejoin="round"/></svg><span>&amp; Others</span></li>
  </ul>

  <div class="perks">
    <p class="perk">Prompt<br><em>Appointments</em></p>
    <p class="perk">Virtual and<br><em>In-Person Visits</em></p>
  </div>

  <p class="contact phone"><svg viewBox="0 0 22 22"><circle cx="11" cy="11" r="11" fill="#128f7c"/><path d="M6 9c0-2 2.5-3 5-3s5 1 5 3l-2 .5-.5-1.5h-5L8 9.5z M7.5 10.5h7l1 4.5h-9z" fill="#0b1a16"/></svg>(208)555-7193</p>
  <p class="contact address"><svg viewBox="0 0 22 22"><circle cx="11" cy="11" r="11" fill="#128f7c"/><path d="M5.5 11L11 6l5.5 5M7.5 10v5.5h7V10" fill="none" stroke="#0b1a16" stroke-width="1.6" stroke-linejoin="round"/><rect x="9.8" y="12" width="2.4" height="3.5" fill="#0b1a16"/></svg>412 E Marlowe Coeur d'Alene</p>

  <div class="hours-pill">OPENING HOURS</div>
  <p class="hours">MON - THUR : 7AM - 6PM</p>
  <p class="website">www.BrightLoftCare.com</p>
</main>
</body>
</html>
```